Maple Beacon Website

We are starting a marketing company and to do that we need a website! We want a website that will inspire and persuade to bring out the awesomeness in our clients.
What we want to see:
- Inspirational and persuasive imagery that relate to Branding.
- No cliche images eg. business man, suits and hand shakes
- We want to transform and educate our clients.
- We want to show them the path and would like our website to really act as a guide that guides them step by step through our process.
- We want the portray that we are an investment but not have a pretentious way to it. We put our heart into every project and that is how we treat our clients.
-When you submit your design please include what platform you have created for. Preference would be Wordpress or Joobla.

We have included the psd file for the wire frame, logo files, font files, site map and a link to a video we create to give you more information on what we would like to see. http://clipvault.example/t/qk82LmZpr

Feel free to make small modification to the logos if you think it will improve it. Your creativity and advice is most welcome.
Updates

One thing we forgot. We would like to have our contact information near the top of the website as well as at the bottom.  Here is out contact info:

Email: info@maplebeacon.example
Phone: 587-555-0142

Project Deadline Extended
Reason: As we are new with the platform and that we want to optimize our results, we decided to extend the deadline by 15 days. Thanks!

Target Market(s)

28-60, Male and Female, Oil field, Local Businesses, Dentists, Chiropractors, Hair salon, Construction/Renovation, Events etc

Industry/Entity Type

Investment

Requirements
Must have
• - 4 Inspirational and persuasive Imagery for the top portion of the website
- Must have a feel as if your not on a website an example of this is linked below.
http://www.artbidhub.example/design/402957/web-design-by-lena-torvik
Nice to have
• - Creative advice from you.
- Creative buttons for Get Free Quote and Subscribe buttons. Something out of the box that draws peoples attention. eg. a 'B' button. Just and example but still something related to branding.
Should not have
• No Cliches

```html
<!DOCTYPE html>
<html lang="en">
<head>
<meta charset="utf-8">
<title>Maple Beacon</title>
<link rel="stylesheet" href="https://fonts.googleapis.com/css2?family=Open+Sans:ital,wght@0,400;0,600;0,700;0,800;1,600&family=Acme&display=swap">
<style>
:root{
  --ink:#2b2b2b;
  --text:#555;
  --muted:#666;
  --green:#5c8c12;
  --green-bright:#8cc63f;
  --green-dark:#3f7d12;
  --beige:#e9e3d3;
  --beige-light:#f3efe5;
  --page:#f8f8f8;
  --panel:#e6e6e6;
  --photo-tone:#dcd6c2;
  --white:#fff;
}
*{box-sizing:border-box;margin:0;padding:0}
html,body{width:1200px;height:1113px;overflow:hidden;background:var(--page)}
body{font-family:"Open Sans",Arial,sans-serif;color:var(--text)}
.site{position:relative;width:1200px;height:1113px;overflow:hidden;background:var(--page)}

.topbar{position:absolute;left:0;top:0;width:1200px;height:42px;
  background:linear-gradient(#9a9a90,#5e5e56 70%,#4a4a44);color:var(--white);
  display:flex;justify-content:flex-end;align-items:center;padding-right:18px;font-size:17px}
.contact-line{display:flex;align-items:center;gap:5px;white-space:nowrap}
.contact-line strong{font-weight:700}
.icon{width:16px;height:14px}
.topbar .icon,.footer .icon{fill:#111}

.hero{position:absolute;left:0;top:42px;width:1200px;height:380px;
  background:radial-gradient(ellipse at 55% 20%,var(--beige-light),var(--beige) 55%,#ddd6c3)}
.hero-photo{position:absolute;left:490px;top:0;width:280px;height:380px;
  background:linear-gradient(var(--beige-light),var(--photo-tone))}
.sidebar{position:absolute;left:118px;top:0;width:230px;height:330px;
  background:linear-gradient(#fff,#ececec 60%,rgba(236,236,236,0))}
.brand{display:flex;align-items:center;gap:8px;margin:30px 0 0 16px}
.brand-dot{width:12px;height:12px;border-radius:50%;background:#8a8a8a}
.brand-name{font-weight:800;font-size:27px;color:#7a7a7a;line-height:1}
.tagline{margin:28px 0 0 44px;font-style:italic;font-weight:600;font-size:13px;color:#333}
.main-nav{list-style:none;margin:27px 0 0 17px}
.main-nav li{font-weight:700;font-size:16px;color:#333;height:37.5px;letter-spacing:.3px}

.steps{position:absolute;right:18px;top:47px;list-style:none;text-align:right}
.steps li{font-family:"Acme",sans-serif;font-size:18px;color:var(--ink);height:69px;
  display:flex;align-items:center;justify-content:flex-end;gap:7px;text-transform:uppercase}
.step-dot{width:17px;height:17px;border-radius:50%;background:radial-gradient(circle at 35% 35%,#ccc,#777)}
.steps li.active{color:var(--green)}
.steps li.active .step-dot{background:radial-gradient(circle at 35% 35%,#c4ec7e,#5c9b1e)}

.panel{position:absolute;top:447px;height:94px;background:var(--panel);box-shadow:0 14px 10px -8px rgba(0,0,0,.18)}
.connect{left:120px;width:228px;text-align:center}
.panel-title{font-weight:700;font-size:20px;color:var(--muted);margin-top:17px;white-space:nowrap}
.socials{display:flex;justify-content:center;gap:7px;margin-top:5px}
.social{width:31px;height:31px;border-radius:4px;background:#8a8a8a}
.newsletter{left:361px;width:711px}
.newsletter .panel-title{font-size:22px;margin-top:10px;margin-left:54px}
.newsletter .panel-title em{font-style:normal;color:var(--green)}
.subscribe-form{display:flex;gap:4px;margin:6px 0 0 54px}
.email-field{width:521px;height:39px;border:1px solid #ccc;border-radius:3px;background:linear-gradient(#eee,#fff);
  font-size:14px;color:#555;padding:6px 9px}
.btn-subscribe{width:98px;height:37px;border-radius:3px;background:linear-gradient(#c2c2c2,#8d8d8d);
  color:var(--white);font-weight:700;font-size:16px;display:flex;align-items:center;justify-content:center;margin-top:1px}

.welcome{position:absolute;left:123px;top:580px;width:960px}
.welcome h1{font-family:"Acme",sans-serif;font-weight:400;font-size:26px;color:var(--ink);text-transform:uppercase}
.welcome h2{font-weight:700;font-size:16px;color:var(--green);margin:12px 0 0 2px;line-height:21px}
.welcome p{font-size:15.7px;line-height:21px;margin-left:2px}
.checklist{list-style:none;margin:6px 0 0 2px}
.checklist li{display:flex;align-items:center;gap:10px;height:34.5px;font-size:16px;color:#444}
.tick{width:20px;height:20px}
.closing{margin-top:14px}
.btn-quote{position:absolute;left:919px;top:831px;width:157px;height:40px;border-radius:3px;
  background:linear-gradient(var(--green-bright),var(--green-dark));color:var(--white);font-weight:700;font-size:16px;
  display:flex;align-items:center;justify-content:center;box-shadow:0 1px 2px rgba(0,0,0,.3)}

.footer{position:absolute;left:0;top:994px;width:1200px;height:119px;
  background:linear-gradient(#a8a8a8,#6a6a6a 50%,#3a3a3a);color:var(--white)}
.footer-nav{position:absolute;left:123px;top:31px;display:flex;gap:13px;list-style:none;font-weight:600;font-size:16px}
.copyright{position:absolute;left:123px;top:58px;font-size:17px;color:var(--green-bright)}
.footer .contact-line{position:absolute;right:124px;top:33px;font-size:18px}
</style>
</head>
<body>
<div class="site">
  <header class="topbar">
    <span class="contact-line">
      <svg class="icon" viewBox="0 0 16 12"><path d="M0 0h16v1.5L8 7 0 1.5z"/><path d="M0 3.5l8 5.5 8-5.5V12H0z"/></svg>
      info@maplebeacon.example&nbsp;|&nbsp;
      <svg class="icon" viewBox="0 0 16 16"><path d="M3 1l3 3-1.8 2.2c1 2 2.6 3.6 4.6 4.6L11 9l3 3-2 3C6 14 2 10 1 3z"/></svg>
      <strong>587-555-0142</strong>
    </span>
  </header>

  <section class="hero">
    <div class="hero-photo" role="img" aria-label="Photo of a smiling child measuring his height against a growth chart"></div>
    <nav class="sidebar">
      <div class="brand"><span class="brand-dot"></span><span class="brand-name">Maple Beacon</span></div>
      <p class="tagline">Because You're Awesome!</p>
      <ul class="main-nav">
        <li>STRATEGY</li><li>PORTFOLIO</li><li>ABOUT US</li><li>CONTACT US</li><li>BLOG</li>
      </ul>
    </nav>
    <ul class="steps">
      <li>Maple Beacon<span class="step-dot"></span></li>
      <li>Be Found<span class="step-dot"></span></li>
      <li>Connect<span class="step-dot"></span></li>
      <li class="active">Get Growing<span class="step-dot"></span></li>
    </ul>
  </section>

  <aside class="panel connect">
    <div class="panel-title">CONNECT WITH US</div>
    <div class="socials" aria-label="Social links">
      <span class="social"></span><span class="social"></span><span class="social"></span><span class="social"></span><span class="social"></span>
    </div>
  </aside>

  <aside class="panel newsletter">
    <div class="panel-title"><em>GET TIPS AND TRICKS!</em> SUBSCRIBE TO OUR NEWSLETTER</div>
    <div class="subscribe-form">
      <div class="email-field">your email id</div>
      <div class="btn-subscribe">Subscribe</div>
    </div>
  </aside>

  <main class="welcome">
    <h1>Welcome to Maple Beacon</h1>
    <h2>Our Mission</h2>
    <p>Etiam adipiscing mollis nulla, ac bibendum elit commodo ac. Pellentesque vehicula sodales vulputate. Suspendisse vel semper tortor. Duis tristique pharetra ligula sed bibendum. Etiam adipiscing mollis nulla, ac bibendum elit commodo ac. Etiam adipiscing mollis nulla, ac bibendum elit commodo ac.</p>
    <ul class="checklist">
      <li><svg class="tick" viewBox="0 0 20 20"><rect width="20" height="20" rx="3" fill="#8cc63f"/><path d="M5 10.5l3.2 3L15 6.5" stroke="#fff" stroke-width="2.6" fill="none" stroke-linecap="round" stroke-linejoin="round"/></svg>Nam ac risus metus, sit amet blandit ante.</li>
      <li><svg class="tick" viewBox="0 0 20 20"><rect width="20" height="20" rx="3" fill="#8cc63f"/><path d="M5 10.5l3.2 3L15 6.5" stroke="#fff" stroke-width="2.6" fill="none" stroke-linecap="round" stroke-linejoin="round"/></svg>Nunc adipiscing, ipsum eu scelerisque euismod, diam nisl condimentum neque,</li>
      <li><svg class="tick" viewBox="0 0 20 20"><rect width="20" height="20" rx="3" fill="#8cc63f"/><path d="M5 10.5l3.2 3L15 6.5" stroke="#fff" stroke-width="2.6" fill="none" stroke-linecap="round" stroke-linejoin="round"/></svg>Vel gravida ligula velit vitae nisl. Pellentesque at dignissim ipsum. Vivamus id massa arcu.</li>
      <li><svg class="tick" viewBox="0 0 20 20"><rect width="20" height="20" rx="3" fill="#8cc63f"/><path d="M5 10.5l3.2 3L15 6.5" stroke="#fff" stroke-width="2.6" fill="none" stroke-linecap="round" stroke-linejoin="round"/></svg>Phasellus feugiat condimentum neque ac bibendum.</li>
      <li><svg class="tick" viewBox="0 0 20 20"><rect width="20" height="20" rx="3" fill="#8cc63f"/><path d="M5 10.5l3.2 3L15 6.5" stroke="#fff" stroke-width="2.6" fill="none" stroke-linecap="round" stroke-linejoin="round"/></svg>Pellentesque dictum lectus sapien, eu pulvinar eros.</li>
    </ul>
    <p class="closing">Maecenas lacinia, nulla at interdum dapibus, velit sapien posuere eros, et hendrerit purus erat quis est. Proin commodo blandit mauris sed convallis. Donec tellus metus, feugiat sed condimentum congue, dignissim ut leo.</p>
  </main>

  <div class="btn-quote">Get a Free Quote!</div>

  <footer class="footer">
    <ul class="footer-nav">
      <li>Site Map</li><li>Strategy</li><li>Portfolio</li><li>About Us</li><li>Contact Us</li><li>Blog</li>
    </ul>
    <div class="copyright">©MAPLE BEACON INC. 2013</div>
    <span class="contact-line">
      <svg class="icon" viewBox="0 0 16 12"><path d="M0 0h16v1.5L8 7 0 1.5z"/><path d="M0 3.5l8 5.5 8-5.5V12H0z"/></svg>
      info@maplebeacon.example&nbsp;|&nbsp;
      <svg class="icon" viewBox="0 0 16 16"><path d="M3 1l3 3-1.8 2.2c1 2 2.6 3.6 4.6 4.6L11 9l3 3-2 3C6 14 2 10 1 3z"/></svg>
      <strong>587-555-0142</strong>
    </span>
  </footer>
</div>
</body>
</html>
```